Harbor Crestline (Business Card Design)

Need business cards designed. Something modern, chic, and sleek. Mabye the back of the card should be the navy blue that is in the logo and then just the logo on the back.

Target Market(s)

Those in the hotel, office, and renovation industry

Contact Information for Business Card

1. Logo 2. Dorian Fenwick 3. CEO/Founder 4. Phone: (833) HarbCre / (833) 427-2731 5. Email: dorian@theharborcrestline.com 6. Website: www.theharborcrestline.com

Font styles to use
Other font styles liked:
• Look at the logo font and base the font for everything else off of that.

Colors
0054AA
0677BA
7BADD7
CADEEF
E8F1F8

Requirements
Must have
• Colors that are associated in the logo
Nice to have
• Sleek modern clean and chic design.

```html
<!DOCTYPE html>
<html lang="en">
<head>
<meta charset="utf-8">
<title>Harbor Crestline — Business Card</title>
<link rel="stylesheet" href="https://fonts.googleapis.com/css2?family=Open+Sans:wght@400;600;700&display=swap">
<style>
  :root {
    --navy: #0b1747;
    --navy-deep: #070f33;
    --navy-sheen: #3a3f86;
    --white: #ffffff;
    --gold: #c9a23c;
    --gold-dark: #a8842a;
    --backdrop: #26272b;
  }
  * { box-sizing: border-box; margin: 0; padding: 0; }
  html, body {
    width: 1200px; height: 780px; overflow: hidden;
    background: var(--backdrop);
    font-family: "Open Sans", Arial, sans-serif;
  }
  .canvas {
    width: 1200px; height: 780px;
    display: flex; align-items: center; justify-content: center; gap: 40px;
  }
  .card {
    position: relative;
    width: 560px; height: 320px;
    background: var(--navy);
    border-radius: 6px;
    overflow: hidden;
    box-shadow: 0 10px 30px rgba(0,0,0,.45);
  }

  /* Front */
  .brand-mark-area {
    position: absolute; left: 28px; top: 40px;
    width: 200px; height: 210px;
    border-radius: 4px;
    background: linear-gradient(100deg, var(--navy-deep) 0%, #141e55 55%, var(--navy-sheen) 85%, #c9cbe6 100%);
    opacity: .85;
  }
  .front-content {
    position: absolute; left: 260px; top: 34px; right: 40px;
    color: var(--white);
  }
  .wordmark {
    display: flex; align-items: center; gap: 10px;
    font-weight: 700; color: var(--white);
    letter-spacing: .08em; text-transform: uppercase;
  }
  .wordmark__square { width: 14px; height: 14px; background: var(--white); flex: none; }
  .wordmark--small { font-size: 19px; }
  .person-name {
    margin-top: 30px;
    font-size: 28px; font-weight: 700; color: var(--gold); line-height: 1.1;
  }
  .person-role { font-size: 14px; font-weight: 600; margin-top: 4px; }
  .address { margin-top: 14px; font-size: 12.5px; line-height: 1.5; }
  .contact-list { list-style: none; margin-top: 10px; font-size: 12.5px; line-height: 1.75; }
  .contact-list li { display: flex; align-items: center; gap: 8px; }
  .contact-icon { width: 13px; height: 13px; flex: none; }
  .gold-tab {
    position: absolute; right: 0; top: 150px;
    width: 14px; height: 70px;
    background: linear-gradient(180deg, var(--gold) 0%, var(--gold-dark) 100%);
  }

  /* Back */
  .back-pattern-area {
    position: absolute; inset: 0;
    background: linear-gradient(115deg, var(--navy) 0%, #0e1b52 50%, #2a3274 78%, #8c92c4 100%);
  }
  .back-center {
    position: absolute; inset: 0;
    display: flex; align-items: center; justify-content: center;
  }
  .wordmark--large { font-size: 30px; gap: 14px; }
  .wordmark--large .wordmark__square { width: 22px; height: 22px; }
</style>
</head>
<body>
<main class="canvas">

  <section class="card card--front" aria-label="Card front">
    <div class="brand-mark-area" role="img" aria-label="Large embossed brand symbol in navy with silver sheen"></div>
    <div class="front-content">
      <div class="wordmark wordmark--small"><span class="wordmark__square"></span>Harbor Crestline</div>
      <p class="person-name">Dorian Fenwick</p>
      <p class="person-role">CEO/Founder</p>
      <p class="address">4120 Larkspur Ave<br>Suite 210, Ridgefield, MD 21190</p>
      <ul class="contact-list">
        <li>
          <svg class="contact-icon" viewBox="0 0 24 24" aria-hidden="true"><path fill="var(--gold)" d="M6.6 10.8a15.1 15.1 0 0 0 6.6 6.6l2.2-2.2a1 1 0 0 1 1-.25 11.4 11.4 0 0 0 3.6.57 1 1 0 0 1 1 1V20a1 1 0 0 1-1 1A17 17 0 0 1 3 4a1 1 0 0 1 1-1h3.5a1 1 0 0 1 1 1c0 1.25.2 2.45.57 3.57a1 1 0 0 1-.25 1z"/></svg>
          (833) HarbCre / (833) 427-2731
        </li>
        <li>
          <svg class="contact-icon" viewBox="0 0 24 24" aria-hidden="true"><circle cx="12" cy="12" r="10" fill="none" stroke="var(--gold)" stroke-width="2"/><path d="M2 12h20M12 2c3 3 3 17 0 20M12 2c-3 3-3 17 0 20" fill="none" stroke="var(--gold)" stroke-width="1.6"/></svg>
          www.theharborcrestline.com
        </li>
        <li>
          <svg class="contact-icon" viewBox="0 0 24 24" aria-hidden="true"><rect x="2" y="5" width="20" height="14" rx="1.5" fill="var(--gold)"/><path d="M3 6l9 7 9-7" fill="none" stroke="var(--navy)" stroke-width="1.8"/></svg>
          dorian@theharborcrestline.com
        </li>
      </ul>
    </div>
    <div class="gold-tab"></div>
  </section>

  <section class="card card--back" aria-label="Card back">
    <div class="back-pattern-area" role="img" aria-label="Repeating brand symbol pattern in navy with a silver sheen toward the right"></div>
    <div class="back-center">
      <div class="wordmark wordmark--large"><span class="wordmark__square"></span>Harbor Crestline</div>
    </div>
  </section>

</main>
</body>
</html>
```